Shipping and Logistics, Project

Project description : Company Profile

A total logistics company covering domestic / international freight forwarding, warehouse management services, haulage, supply chain management, transport management & distribution, procurement & assembly services, shipping, chartering & bunker services, project logistics & tax exemption consultancy, oil & gas logistics, halal logistics services & integrated logistics management. We’re a well-established and experienced freight forwarder in Kuala Lumpur, Malaysia. We specialize in customized value-added solution that optimizes your supply chain by trimming inventory, reducing logistics cost and enhancing your customer service levels.

As a member of the Worldwide Parcel and Carriage Alliance which comprise of 170 global freight agents in 80 countries that promotes great handling in cross-trade logistics and freighting. You could rely on our efficiency in handlings of export cargo (FCL, LCL, Bulk and Conventional) between our global network offices worldwide with a total scale of 10,000 groomed specialists in various logistics division working together to ensure delivery task meets with your expectation. With our dedicated qualified and experienced professionals, we are fully committed to serving our clients.

Our generic services are listed below for your reference:

• Air Freight
• Ocean Freight FCL & LCL
• Container Haulage
• Warehousing
• Transportation and Distribution within Malaysia and Thailand
• Cross-Border Road Line-hauls between Thailand, Malaysia, Singapore and Laos
• Customs Brokerage and Forwarding
• Project Cargo Freight Forwarding for setting up of new plants / factories and ad hoc heavy-lift
• Air-Sea-Road-Rail multi-modal options
• Import / Export / Storage / Documentation / Handling of DG / Hazmat
• Vessel and Aircraft Charters

Our Mission
Based on the motto “Quick, Reliable and Polite”, we are dedicated to upholding the following three points corporate philosophy:
1. Adhering to the principle that “the customer always comes first”.
2. Contributing to the development of the local community.
3. Making it our duty to be responsible and sincere.

Our Edge
• One-Stop Logistics Solutions
• Extensive Network Throughout Malaysia
• Highly Qualified and Experienced Pool of Professionals
• Comprehensive IT Solutions
• Innovative and Customer-focused Solutions
• Flexible and Consistent in Managing Exceptions
• Total Supply Chain Visibility

Target Market
1. We sell the logistics services to all the industry in Malaysia and Worldwide. (ONE Stop Logistics Solutions)

Competitor
1. TR Valmont
2. Corvessa Transport
3. Brandt + Loewe
4. FELRO
5. QTV
6. Routemarks
7. Ilto Logistics

Rules for Picking a Company Name
1. Unique and unforgettable
2. Avoid unusual spellings
3. Easy to pronounce and remember
4. Keep it simple
5. Make some sense
6. Give a clue

Rules for Picking a Company Logo
4. Keep it simple
5. Make some sense
6. Give a clue

1. Simplicity
2. Memorability
3. Originality
4. Modern Yet Timeless
5. Balance
6. Complementary
7. Versatility

Stationery Information
1. Company Name : ZENFreight Solutions Sdn Bhd
2. Company Registration : 2837165-W
3. Address : 42-08, Jalan Cempaka Indah 5, Taman Seri Bayu, 81300 Johor Bahru, Johor, Malaysia.
4. Name : Derek Tan
5. Position : Manager
6. Mobile No : (+6019) 4381907
7. Office No : (+607) 5218764
8. Fax No : Not Available
9. Email Address : derek.tan@zenfreight-solutions.example
10. Web Domain : www.zenfreight-solutions.example
11. Company Slogan : Be Globally Connected

Target Market(s)

Corporate Company

Industry/Entity Type

Shipping and Logistics Industry

Requirements
Must have
• Company Full Name : ZENFREIGHT SOLUTIONS SDN. BHD.
Nice to have
• Keep it simple and unforgettable ...

```html
<!DOCTYPE html>
<html lang="en">
<head>
<meta charset="utf-8">
<title>ZENFreight Solutions – Business Card</title>
<link rel="stylesheet" href="https://fonts.googleapis.com/css2?family=Poppins:wght@400;500;600&family=Didact+Gothic&display=swap">
<style>
  :root {
    --brand-blue: #2e8ad9;
    --deep-navy: #2a3a4f;
    --mid-blue: #2c6aa8;
    --ink: #222222;
    --paper: #ffffff;
    --backdrop: #e6e8eb;
    --rule: #9a9a9a;
  }
  * { margin: 0; padding: 0; box-sizing: border-box; }
  html, body { width: 1200px; height: 1200px; overflow: hidden; }
  body { background: var(--backdrop); position: relative; font-family: "Poppins", sans-serif; }

  .card { position: absolute; top: 303px; width: 369px; height: 594px; overflow: hidden; }

  /* Front */
  .card-front { left: 200px; background: var(--brand-blue); color: var(--paper); }
  .front-backdrop {
    position: absolute; inset: 0;
    background:
      radial-gradient(ellipse 70% 55% at 35% 45%, rgba(46,138,217,0.95), rgba(46,138,217,0) 70%),
      linear-gradient(150deg, var(--mid-blue) 0%, var(--brand-blue) 35%, var(--brand-blue) 60%, var(--mid-blue) 80%, var(--deep-navy) 100%);
  }
  .front-backdrop::after {
    content: ""; position: absolute; inset: 0;
    background: linear-gradient(210deg, var(--deep-navy) 0%, rgba(42,58,79,0) 30%);
  }
  .brand-lockup { position: absolute; display: flex; align-items: center; gap: 14px; }
  .brand-mark { width: 62px; height: 62px; border: 5px solid currentColor; flex: none; }
  .brand-name { font-family: "Poppins", sans-serif; font-weight: 600; line-height: 1; }
  .brand-name .line-main { display: block; font-size: 27px; letter-spacing: 0.5px; }
  .brand-name .line-sub { display: block; font-size: 11.5px; letter-spacing: 2.2px; margin-top: 7px; }

  .card-front .brand-lockup { left: 34px; top: 565px; top: 262px; color: var(--paper); }
  .registration { position: absolute; top: 660px; top: 359px; left: 0; width: 100%; text-align: center; font-size: 17px; font-weight: 400; }
  .slogan { position: absolute; top: 534px; left: 0; width: 100%; text-align: center; font-size: 16.5px; font-weight: 500; letter-spacing: 0.2px; }

  /* Back */
  .card-back { left: 599px; width: 364px; background: var(--paper); color: var(--ink); }
  .card-back .brand-lockup { left: 36px; top: 80px; color: var(--brand-blue); }

  .person { position: absolute; top: 270px; width: 100%; text-align: center; }
  .person-name { font-size: 26px; font-weight: 600; line-height: 1.1; letter-spacing: 0.3px; }
  .person-name .surname { color: var(--brand-blue); }
  .person-role { font-size: 16px; font-weight: 400; margin-top: 2px; letter-spacing: 0.3px; }

  .icon-row { position: absolute; top: 337px; left: 0; width: 100%; display: flex; justify-content: center; align-items: center; gap: 4px; }
  .icon-row .rule { width: 31px; height: 1px; background: var(--rule); margin: 0 4px; }
  .icon-tile { width: 25px; height: 25px; border-radius: 3px; background: var(--brand-blue); display: flex; align-items: center; justify-content: center; }
  .icon-tile svg { width: 17px; height: 17px; }

  .contact-list { position: absolute; top: 374px; width: 100%; text-align: center; font-family: "Didact Gothic", sans-serif; font-size: 17.5px; line-height: 21.7px; list-style: none; }
  .contact-list .email { font-size: 15.5px; }
  .contact-list .web { font-size: 16.5px; }
  .contact-list .web-domain { color: var(--brand-blue); }

  .divider { position: absolute; top: 478px; left: 89px; width: 194px; height: 1px; background: var(--rule); }

  .address { position: absolute; top: 492px; width: 100%; text-align: center; font-family: "Didact Gothic", sans-serif; font-style: normal; font-size: 17.5px; line-height: 21.7px; }
</style>
</head>
<body>

<section class="card card-front">
  <div class="front-backdrop" role="img" aria-label="Soft blue gradient background with faint layered chevron shapes"></div>
  <div class="brand-lockup">
    <span class="brand-mark"></span>
    <span class="brand-name">
      <span class="line-main">ZENFREIGHT</span>
      <span class="line-sub">SOLUTIONS SDN. BHD.</span>
    </span>
  </div>
  <p class="registration">Registration : 2837165-W</p>
  <p class="slogan">BE GLOBALLY CONNECTED</p>
</section>

<section class="card card-back">
  <div class="brand-lockup">
    <span class="brand-mark"></span>
    <span class="brand-name">
      <span class="line-main">ZENFREIGHT</span>
      <span class="line-sub">SOLUTIONS SDN. BHD.</span>
    </span>
  </div>

  <div class="person">
    <h1 class="person-name">DEREK <span class="surname">TAN</span></h1>
    <p class="person-role">MANAGER</p>
  </div>

  <div class="icon-row">
    <span class="rule"></span>
    <span class="icon-tile" aria-label="Mobile">
      <svg viewBox="0 0 16 16" fill="none" stroke="#fff" stroke-width="1.4"><rect x="4.5" y="1.5" width="7" height="13" rx="1"/><circle cx="8" cy="12.3" r="0.6" fill="#fff"/></svg>
    </span>
    <span class="icon-tile" aria-label="Office phone">
      <svg viewBox="0 0 16 16" fill="#fff"><path d="M1.5 6.5 C1.5 3.5 14.5 3.5 14.5 6.5 L14.5 7.5 L11 7.5 L11 6 L5 6 L5 7.5 L1.5 7.5 Z"/><path d="M4 8.5 L12 8.5 L13.5 13.5 L2.5 13.5 Z"/></svg>
    </span>
    <span class="icon-tile" aria-label="Email">
      <svg viewBox="0 0 16 16" fill="none" stroke="#fff" stroke-width="1.3"><rect x="1.5" y="3.5" width="13" height="9"/><path d="M1.5 3.5 L8 9 L14.5 3.5 M1.5 12.5 L6.2 7.5 M14.5 12.5 L9.8 7.5"/></svg>
    </span>
    <span class="icon-tile" aria-label="Website">
      <svg viewBox="0 0 16 16" fill="none" stroke="#fff" stroke-width="1.3"><circle cx="8" cy="8" r="6.2"/><ellipse cx="8" cy="8" rx="2.6" ry="6.2"/><path d="M1.8 8 H14.2"/></svg>
    </span>
    <span class="rule"></span>
  </div>

  <ul class="contact-list">
    <li>(+6019) 4381907</li>
    <li>(+607) 5218764</li>
    <li class="email">derek.tan@zenfreight-solutions.example</li>
    <li class="web">www.<span class="web-domain">zenfreight-solutions</span>.example</li>
  </ul>

  <div class="divider"></div>

  <address class="address">
    42-08, Jalan Cempaka Indah 5<br>
    Taman Seri Bayu, 81300 Johor<br>
    Bahru, Johor, Malaysia
  </address>
</section>

</body>
</html>
```